Bluecrest Learning Corps by graduating students from college in two years

Based on the logo design, create stationary and business cards for
Dr. Venrel T Oskamp, CEO, (703) 482-1736
and Marisa Deltoft, Respresentative, (301) 647-2208
Address: 4719 Pellham Court, Faurfax Station, VA 22039
Incorporate elelments of the logo

Target Market(s)

USA

Font styles to use
Other font styles liked:
• match with the logo type style

```html
<!DOCTYPE html>
<html lang="en">
<head>
<meta charset="utf-8">
<title>Bluecrest Learning Corps – Business Card</title>
<link rel="stylesheet" href="https://fonts.googleapis.com/css2?family=Tinos:wght@400;700&display=swap">
<style>
  :root {
    --page-bg: #d8cfc3;
    --card-bg: #f1ebe2;
    --card-edge: #fbf8f3;
    --gold: #d29b2b;
    --navy: #1f2a6b;
    --ink: #2a2420;
  }
  html, body {
    margin: 0;
    padding: 0;
    width: 1200px;
    height: 1047px;
    overflow: hidden;
    background: var(--page-bg);
  }
  .canvas {
    position: relative;
    width: 1200px;
    height: 1047px;
  }
  .business-card {
    position: absolute;
    left: 100px;
    top: 251px;
    width: 1000px;
    height: 545px;
    background: var(--card-bg);
    border: 2px solid var(--card-edge);
    border-radius: 26px;
    box-sizing: border-box;
    font-family: "Tinos", "Times New Roman", serif;
    color: var(--ink);
  }
  .brand {
    position: absolute;
    left: 100px;
    top: 150px;
    width: 310px;
    text-align: center;
  }
  .brand-dot {
    display: block;
    width: 120px;
    height: 120px;
    margin: 0 auto 22px;
    border-radius: 50%;
    background: var(--navy);
  }
  .brand-name {
    font-size: 30px;
    font-weight: 700;
    line-height: 1.15;
    color: var(--navy);
  }
  .divider {
    position: absolute;
    left: 459px;
    top: 127px;
    width: 2px;
    height: 287px;
    background: var(--gold);
  }
  .contact {
    position: absolute;
    left: 519px;
  }
  .person-name {
    margin: 0;
    font-size: 38px;
    font-weight: 700;
    line-height: 1;
    color: var(--gold);
  }
  .person-role {
    font-size: 22px;
    line-height: 1;
    margin-top: 16px;
  }
  .phone {
    display: flex;
    align-items: center;
    gap: 10px;
    font-size: 24px;
    line-height: 1;
    margin-top: 30px;
  }
  .icon { flex: none; }
  .contact-ceo { top: 112px; }
  .contact-rep { top: 285px; }
  .address {
    position: absolute;
    left: 216px;
    top: 482px;
    display: flex;
    align-items: center;
    gap: 10px;
    font-size: 24px;
    line-height: 1;
  }
</style>
</head>
<body>
<div class="canvas">
  <section class="business-card">
    <div class="brand">
      <span class="brand-dot"></span>
      <div class="brand-name">Bluecrest Learning Corps</div>
    </div>

    <div class="divider"></div>

    <div class="contact contact-ceo">
      <h2 class="person-name">Dr. Venrel T Oskamp</h2>
      <div class="person-role">CEO</div>
      <div class="phone">
        <svg class="icon" width="20" height="16" viewBox="0 0 20 16" aria-hidden="true">
          <path d="M1 5 Q10 -1 19 5 L17 8 L14 6 L14 4 Q10 2 6 4 L6 6 L3 8 Z" fill="var(--gold)"/>
          <path d="M5 8 L15 8 L18 15 L2 15 Z" fill="var(--gold)"/>
          <circle cx="10" cy="11.5" r="2" fill="var(--card-bg)"/>
        </svg>
        <span>(703) 482-1736</span>
      </div>
    </div>

    <div class="contact contact-rep">
      <h2 class="person-name">Marisa Deltoft</h2>
      <div class="person-role">Respresentative</div>
      <div class="phone">
        <svg class="icon" width="20" height="16" viewBox="0 0 20 16" aria-hidden="true">
          <path d="M1 5 Q10 -1 19 5 L17 8 L14 6 L14 4 Q10 2 6 4 L6 6 L3 8 Z" fill="var(--gold)"/>
          <path d="M5 8 L15 8 L18 15 L2 15 Z" fill="var(--gold)"/>
          <circle cx="10" cy="11.5" r="2" fill="var(--card-bg)"/>
        </svg>
        <span>(301) 647-2208</span>
      </div>
    </div>

    <div class="address">
      <svg class="icon" width="16" height="22" viewBox="0 0 16 22" aria-hidden="true">
        <path d="M8 0 A8 8 0 0 1 16 8 C16 14 8 22 8 22 C8 22 0 14 0 8 A8 8 0 0 1 8 0 Z" fill="var(--gold)"/>
        <circle cx="8" cy="8" r="3" fill="var(--card-bg)"/>
      </svg>
      <span>4719 Pellham Court, Faurfax Station, VA 22039</span>
    </div>
  </section>
</div>
</body>
</html>
```